KRL Stationery Design Project

Dear Designers,
We need a new stationery design for company to match our new logo.
Designers should provide a design for the following:
1. Business Card: 3.5x2 Inches.
2. Letterhead: A4 size.
3. Envelops: 25x35.5 Cm.
You can keep the Arabic name at the bottom of the logo Or you can use the separate attached Arabic Name.
Please refer to the attached logo guide for design information.
Sample Business Card information:
Name: Tarek Sowan
Position: Operation Manager
Tel: +966 920007164 Ex. 500
Fax: +966 (3)8842617
Mob: +966 (5)00263817
email: tarek@krl-example.com.sa
URL: www.krl-example.com.sa
Address:
Nakheel Heights, Suite 718
Zayed bin Omar Str.
Khobar, 31847
Saudi Arabia
Updates
Dear All,
Please note, we had uploaded our logo along with Arabic writing in Adobe illustrator format (.ai).
Regards,
Karim
Dear All,
A sample data for the business card had been added as per your request.
Regards,
Karim

```html
<!DOCTYPE html>
<html lang="en">
<head>
<meta charset="utf-8">
<title>KRL Business Card</title>
<link rel="stylesheet" href="https://fonts.googleapis.com/css2?family=Source+Sans+3:wght@400;600;700&display=swap">
<style>
  :root {
    --backdrop: #2a2a2c;
    --card: #ffffff;
    --navy: #14325a;
    --ink: #3d3d3f;
    --label: #1b1b1d;
  }
  * { margin: 0; padding: 0; box-sizing: border-box; }
  html, body { width: 960px; height: 1200px; overflow: hidden; }
  body {
    background: var(--backdrop);
    font-family: "Source Sans 3", Arial, sans-serif;
    position: relative;
  }
  .card {
    position: absolute;
    background: var(--card);
    border-radius: 30px;
    box-shadow: 0 6px 14px rgba(0,0,0,0.45);
  }
  .card-front { left: 60px; top: 88px; width: 840px; height: 480px; }
  .card-back  { left: 57px; top: 625px; width: 840px; height: 480px; }

  .brand {
    position: absolute;
    left: 0; right: 0;
    display: flex;
    justify-content: center;
    align-items: center;
    gap: 18px;
    color: var(--navy);
    font-weight: 700;
    letter-spacing: 2px;
    line-height: 1;
  }
  .brand-mark {
    display: inline-block;
    background: var(--navy);
    border-radius: 50%;
  }
  .card-front .brand { top: 120px; font-size: 96px; }
  .card-front .brand-mark { width: 34px; height: 34px; }
  .card-back .brand { top: 170px; font-size: 120px; }
  .card-back .brand-mark { width: 42px; height: 42px; }

  .holder {
    position: absolute;
    top: 293px; left: 0; right: 0;
    text-align: center;
    color: var(--navy);
    font-size: 31px;
    font-weight: 400;
  }
  .holder .role { font-size: 21px; }

  .contact {
    position: absolute;
    top: 352px; left: 0; right: 0;
    text-align: center;
    color: var(--ink);
    font-size: 21px;
    line-height: 30px;
  }
  .contact .key { font-weight: 700; font-style: italic; color: var(--label); }
  .contact .sep { margin: 0 8px; }
</style>
</head>
<body>
  <section class="card card-front">
    <div class="brand"><span class="brand-mark"></span>KRL</div>
    <p class="holder">Your Name, <span class="role">Designation</span></p>
    <div class="contact">
      <p><span class="key">t</span> : 123-123-1234<span class="sep">|</span><span class="key">f</span> : 123-123-1234</p>
      <p><span class="key">e</span> : info@krl-example.com.sa<span class="sep">|</span><span class="key">w</span> : www.krl-example.com.sa</p>
      <p>1234, Suite# 123, Street Name, State Name, Country Code</p>
    </div>
  </section>

  <section class="card card-back">
    <div class="brand"><span class="brand-mark"></span>KRL</div>
  </section>
</body>
</html>
```